eBook Cover_H. Lindqvist-Borna
Schnell und zuverlässoig,Änderungswünsche wurden umgehend ausgeführt. Vielen Dank für das tolle Cover zu meinem ersten Buch!
Zielgruppe
freie Roman-Autorin (Erstlingswerk)
Zielgruppe: Lesende (Erwachsene), Frauen
Charakterisierung: magisch-realistischer Familienroman, spielt im Europa der Jetzt-Zeit
Aufgabenstellung
Im ersten Schritt geht es um ein Cover für ein eBook, das aber bei Bedarf als Book on Demand gedruckt werden soll. Es wird daher später Anforderung bzgl. Dicke / Umfang des gedruckten Buches und einer Rückseite geben. Das gewählte Design soll dann dahingehend überarbeitet und finale Druckdaten zur Verfügung gestellt werden. Dies soll von vornherein berücksichtigt werden und im Preis enthalten sein.
Titel: Regen über Glas, Monde im Moos
Autorinnenname: Henrike Lindqvist-Borna
des weiteren auf dem Cover: Roman

```html
<!DOCTYPE html>
<html lang="de">
<head>
<meta charset="utf-8">
<title>Regen über Glas – Henrike Lindqvist-Borna</title>
<link rel="stylesheet" href="https://fonts.googleapis.com/css2?family=Open+Sans:wght@400&family=Gochi+Hand&display=swap">
<style>
  :root {
    --stage: #e4e4e4;
    --paper: #fbfbfb;
    --frame: #2b2624;
    --ink: #111111;
    --title-red: #e0251a;
    --smoke-dark: #8a8a8a;
    --smoke-mid: #b5b5b5;
    --feather: #e9e2da;
  }
  html, body {
    margin: 0;
    width: 1200px;
    height: 1200px;
    overflow: hidden;
    background: var(--stage);
  }
  .cover {
    position: absolute;
    left: 282px;
    top: 89px;
    width: 636px;
    height: 1021px;
    background: var(--paper);
    overflow: hidden;
    box-shadow: 6px 8px 10px rgba(0, 0, 0, 0.35);
  }
  .cover-art {
    position: absolute;
    inset: 0;
    width: 636px;
    height: 1021px;
  }
  .cover-frame {
    position: absolute;
    inset: 0;
    box-shadow: inset 0 0 0 4px var(--frame), inset 0 0 26px 6px rgba(43, 38, 36, 0.6);
    pointer-events: none;
  }
  .cover p, .cover h1 { margin: 0; }
  .author {
    position: absolute;
    top: 97px;
    left: 0;
    width: 100%;
    text-align: center;
    font: 400 39px/1 "Open Sans", sans-serif;
    color: var(--ink);
  }
  .title {
    position: absolute;
    font-family: "Gochi Hand", cursive;
    font-weight: 400;
    color: var(--title-red);
    line-height: 1;
    white-space: nowrap;
  }
  .title-line-1 { top: 492px; left: 83px; font-size: 150px; }
  .title-line-2 { top: 632px; left: 49px; font-size: 150px; }
  .title-small { font-size: 62px; vertical-align: 0.9em; margin-right: 6px; }
  .subtitle {
    position: absolute;
    top: 810px;
    left: 0;
    width: 100%;
    text-align: center;
    font: 400 52px/1 "Open Sans", sans-serif;
    color: var(--ink);
  }
  .genre {
    position: absolute;
    top: 910px;
    left: 0;
    width: 100%;
    text-align: center;
    font: 400 34px/1 "Open Sans", sans-serif;
    color: var(--ink);
  }
</style>
</head>
<body>
  <main class="cover">
    <svg class="cover-art" viewBox="0 0 636 1021" role="img" aria-label="Illustration: helle Federflügel links, die in grauen Rauch übergehen">
      <defs>
        <filter id="soften" x="-50%" y="-50%" width="200%" height="200%">
          <feGaussianBlur stdDeviation="45"/>
        </filter>
        <filter id="soften-light" x="-50%" y="-50%" width="200%" height="200%">
          <feGaussianBlur stdDeviation="25"/>
        </filter>
      </defs>
      <g filter="url(#soften)">
        <ellipse cx="420" cy="560" rx="200" ry="330" fill="var(--smoke-mid)"/>
        <ellipse cx="440" cy="520" rx="130" ry="230" fill="var(--smoke-dark)"/>
        <ellipse cx="200" cy="260" rx="90" ry="60" fill="var(--smoke-mid)"/>
      </g>
      <g filter="url(#soften-light)">
        <ellipse cx="170" cy="620" rx="130" ry="280" fill="var(--feather)" transform="rotate(20 170 620)"/>
      </g>
    </svg>
    <div class="cover-frame"></div>

    <p class="author">Henrike Lindqvist-Borna</p>
    <h1 class="title title-line-1">Regen</h1>
    <h1 class="title title-line-2"><span class="title-small">über</span>Glas</h1>
    <p class="subtitle">Monde im Moos</p>
    <p class="genre">Roman</p>
  </main>
</body>
</html>
```